Business Card Design needed - Something Awesome!

Need a business card designed. Company is "Marlowe Advisory" we do consulting and also have sales automation technology.
I'm going to use thick stock or metal, something really nice... I was thinking about a QR Code on the back that would just upload my contact info to the persons contact, etc -

This is a Strategy Company with a tech feel. I'm open to ideas but really want this to be nice!

I need a template that should include:

Name | Position or Title
D: 415.902.3376
www.marloweadvisory.example

I'm going to attach my contact so you can use that one, I need to get this printed.

Target Market(s)

Small to mid size customers, Entrepreneurs etc.

Industry/Entity Type

Consulting, Tech, Private Equity.

Contact Information for Business Card

Name, Phone, Maybe email, URL

Font styles to use
Sans Serif

Colors

Designer to choose only greyscale colors for use in the design.

Requirements
Must have
• Fresh, Clean, stand out from the crowd - will be on thick stock or metal.
Nice to have
• Clean, simple yet impactful.
Should not have
• Not cartoonish

```html
<!DOCTYPE html>
<html lang="en">
<head>
<meta charset="utf-8">
<title>Marlowe Advisory — Business Card</title>
<link rel="stylesheet" href="https://fonts.googleapis.com/css2?family=Arimo:wght@400;700&display=swap">
<style>
  :root {
    --bg: #3b3b3b;
    --card: #0d0d0d;
    --card-edge: #1a1a1a;
    --silver: #c9c9c9;
    --silver-soft: #a8a8a8;
    --rule: #5a5a5a;
    --pattern-dark: #050505;
    --pattern-mid: #1c1c1c;
    --pattern-light: #2e2e2e;
  }
  html, body {
    margin: 0;
    padding: 0;
    width: 1200px;
    height: 801px;
    overflow: hidden;
    background: var(--bg);
    font-family: "Arimo", Arial, sans-serif;
  }
  .stage {
    position: relative;
    width: 1200px;
    height: 801px;
  }
  .card {
    position: absolute;
    top: 252px;
    width: 520px;
    height: 297px;
    background: var(--card);
    border: 1px solid var(--card-edge);
    box-sizing: border-box;
    overflow: hidden;
  }
  .card--front { left: 60px; }
  .card--back { left: 620px; }

  /* Front: identity + contacts */
  .identity {
    position: absolute;
    top: 50%;
    left: 0;
    width: 100%;
    transform: translateY(-50%);
    display: flex;
    align-items: center;
    justify-content: center;
    gap: 18px;
  }
  .identity__person { text-align: right; }
  .identity__name {
    margin: 0;
    font-weight: 700;
    font-size: 17px;
    letter-spacing: 0.04em;
    color: var(--silver);
    text-transform: uppercase;
  }
  .identity__title {
    margin: 4px 0 0;
    font-size: 12.5px;
    color: var(--silver-soft);
  }
  .identity__divider {
    width: 1px;
    height: 48px;
    background: var(--rule);
  }
  .contacts {
    list-style: none;
    margin: 0;
    padding: 0;
    font-size: 12.5px;
    color: var(--silver);
    line-height: 1.45;
  }
  .contacts li {
    display: flex;
    align-items: center;
    gap: 6px;
  }
  .contacts svg {
    width: 10px;
    height: 10px;
    fill: var(--silver);
    flex: none;
  }

  /* Back: pattern field + wordmark */
  .pattern-field {
    position: absolute;
    inset: 0;
    background: linear-gradient(120deg, var(--pattern-dark) 0%, var(--pattern-mid) 55%, var(--pattern-light) 100%);
  }
  .wordmark {
    position: absolute;
    left: 0;
    right: 0;
    top: 50%;
    transform: translateY(-50%);
    display: flex;
    align-items: center;
    justify-content: center;
    gap: 10px;
    font-size: 42px;
    font-weight: 400;
    letter-spacing: 0.04em;
    color: var(--silver);
  }
  .wordmark__square {
    width: 14px;
    height: 14px;
    background: var(--silver);
  }
</style>
</head>
<body>
<main class="stage">

  <section class="card card--front" aria-label="Business card front">
    <div class="identity">
      <div class="identity__person">
        <p class="identity__name">Dorian K. Vale</p>
        <p class="identity__title">Founder / CEO</p>
      </div>
      <span class="identity__divider"></span>
      <ul class="contacts">
        <li>
          <svg viewBox="0 0 10 10" aria-hidden="true"><path d="M2 0.5 L3.6 0.5 L4.2 2.8 L3.1 3.7 Q4 5.8 6.3 6.9 L7.2 5.8 L9.5 6.4 L9.5 8 Q9.5 9.5 8 9.5 Q0.5 9 0.5 2 Q0.5 0.5 2 0.5 Z"/></svg>
          415.902.3376
        </li>
        <li>
          <svg viewBox="0 0 10 10" aria-hidden="true"><path d="M0.5 2 H9.5 V8.5 H0.5 Z M1 2.5 L5 5.6 L9 2.5" fill="none" stroke="currentColor"/><path d="M0.5 2 H9.5 L5 5.5 Z"/><path d="M0.5 3 L5 6.3 L9.5 3 V8.5 H0.5 Z"/></svg>
          info@marloweadvisory.example
        </li>
        <li>
          <svg viewBox="0 0 10 10" aria-hidden="true"><circle cx="5" cy="5" r="4.5"/></svg>
          www.marloweadvisory.example
        </li>
      </ul>
    </div>
  </section>

  <section class="card card--back" aria-label="Business card back">
    <div class="pattern-field" role="img" aria-label="Glossy pattern of scattered dark squares across the card"></div>
    <div class="wordmark">
      <span class="wordmark__square" aria-hidden="true"></span>
      <span class="wordmark__name">MARLOWE</span>
    </div>
  </section>

</main>
</body>
</html>
```